Business Card for a mobile physiotherapy company

I need a layout for a business card for a mobile physiotherapy company.
Slogan is "Mobile Physiotherapy - Your Road To Recovery"
Phone number is 867-555-0142
Email VardenTherapy@postnest.ca (subject to change with website)
Website www.VardenTherapy.ca
My name and credentials: Luke Varden Luke Varden, BSc(kin), MPT, CAFCI, IMS
Information maybe included: Direct Billing, Services including Physiotherapy, IMS, acupuncture
Maybe include facebook and instagram logos
One side with the logo clean and sharp
Other side with details, try not to look too busy, keep everything concise

```html
<!DOCTYPE html>
<html lang="en">
<head>
<meta charset="utf-8">
<title>Varden Therapy – Business Card</title>
<link rel="stylesheet" href="https://fonts.googleapis.com/css2?family=Alegreya:wght@400;700&display=swap">
<style>
  :root {
    --navy: #24477a;
    --green: #1b5547;
    --ink: #2d3a4f;
    --card: #f3f3f2;
    --backdrop: #dcdcdc;
    --rule: #d3d6da;
    --band-text: #e9eef2;
  }
  * { margin: 0; padding: 0; box-sizing: border-box; }
  html, body { width: 1200px; height: 576px; overflow: hidden; }
  body {
    background: var(--backdrop);
    font-family: "Alegreya", Georgia, serif;
    color: var(--ink);
    position: relative;
  }
  .card {
    position: absolute;
    top: 139px;
    width: 484px;
    height: 291px;
    background: var(--card);
    border-radius: 12px;
    overflow: hidden;
    box-shadow: 0 2px 6px rgba(0,0,0,0.18);
  }
  .card--front { left: 82px; }
  .card--back { left: 602px; }

  .brand { display: flex; flex-direction: column; align-items: center; }
  .brand__mark { border-radius: 50%; background: var(--navy); }
  .brand__name {
    font-weight: 700;
    color: var(--navy);
    text-align: center;
    white-space: nowrap;
    line-height: 1.1;
  }
  .card--front .brand { position: absolute; left: 0; right: 0; top: 62px; }
  .card--front .brand__mark { width: 58px; height: 58px; margin-bottom: 22px; }
  .card--front .brand__name { font-size: 32px; }

  .services {
    position: absolute; left: 0; right: 0; top: 259px;
    text-align: center; font-size: 13.5px; color: var(--navy);
    white-space: nowrap;
  }
  .services .sep { margin: 0 5px; }
  .card--front .edge {
    position: absolute; left: 0; right: 0; bottom: 0; height: 6px;
    background: linear-gradient(90deg, var(--green), var(--navy));
  }

  .card--back .brand { position: absolute; left: 28px; width: 190px; top: 78px; }
  .card--back .brand__mark { width: 48px; height: 48px; margin-bottom: 18px; }
  .card--back .brand__name { font-size: 26px; }
  .divider {
    position: absolute; left: 238px; top: 70px; width: 1px; height: 130px;
    background: var(--rule);
  }
  .details { position: absolute; left: 269px; top: 64px; }
  .details__name { font-size: 21px; font-weight: 700; color: var(--navy); letter-spacing: 0.5px; line-height: 1.2; }
  .details__creds { font-size: 11.5px; margin-top: 2px; }
  .details__social { font-size: 13.5px; margin-top: 17px; display: flex; align-items: center; gap: 5px; }
  .details__social .mark { width: 19px; height: 19px; border-radius: 50%; }
  .details__social .mark--first { background: var(--navy); margin-left: 2px; }
  .details__social .mark--second { background: var(--green); }
  .contact { list-style: none; margin-top: 6px; font-size: 13.5px; }
  .contact li { display: flex; align-items: center; gap: 16px; height: 18px; }
  .contact svg { width: 11px; height: 11px; fill: var(--ink); flex: none; }
  .band {
    position: absolute; left: 0; right: 0; bottom: 0; height: 28px;
    background: linear-gradient(90deg, var(--green), var(--navy));
    color: var(--band-text);
    font-size: 13.5px; text-align: center; line-height: 28px;
  }
</style>
</head>
<body>
  <section class="card card--front" aria-label="Business card front">
    <div class="brand">
      <div class="brand__mark"></div>
      <div class="brand__name">Varden Therapy</div>
    </div>
    <p class="services">Direct Billing<span class="sep">|</span>Services Including Physiotherapy<span class="sep">|</span>IMS<span class="sep">|</span>Acupuncture</p>
    <div class="edge"></div>
  </section>

  <section class="card card--back" aria-label="Business card back">
    <div class="brand">
      <div class="brand__mark"></div>
      <div class="brand__name">Varden Therapy</div>
    </div>
    <div class="divider"></div>
    <div class="details">
      <h1 class="details__name">LUKE VARDEN</h1>
      <p class="details__creds">BSc(kin), MPT, CAFCI, IMS</p>
      <p class="details__social">Follow us on: <span class="mark mark--first"></span><span class="mark mark--second"></span></p>
      <ul class="contact">
        <li><svg viewBox="0 0 16 16" aria-hidden="true"><path d="M3 1h3l1.5 4-2 1.2a9 9 0 0 0 4.3 4.3L11 8.5l4 1.5v3a2 2 0 0 1-2 2A12 12 0 0 1 1 3a2 2 0 0 1 2-2z"/></svg>867-555-0142</li>
        <li><svg viewBox="0 0 16 16" aria-hidden="true"><path d="M1 3h14v10H1z M1.5 3.5 8 9l6.5-5.5" stroke="#f3f3f2" stroke-width="1.2"/></svg>VardenTherapy@postnest.ca</li>
        <li><svg viewBox="0 0 16 16" aria-hidden="true"><circle cx="8" cy="8" r="7"/><path d="M1 8h14M8 1c-3 3.5-3 10.5 0 14M8 1c3 3.5 3 10.5 0 14" stroke="#f3f3f2" stroke-width="1" fill="none"/></svg>www.VardenTherapy.ca</li>
      </ul>
    </div>
    <div class="band">Mobile Physiotherapy - Your Road To Recovery</div>
  </section>
</body>
</html>
```